Business Cards for new orthopaedic surgery practice

My husband and I are starting our own orthopaedic surgery practice. We are looking for a business card that is uniform, but one will have my name/title and the other will have his. You can just create one design with my name on it for now. But when I choose your design as the winning design I will ask that you add another copy with his name/title.

We are looking for classy, simple, elite all in one. We like dark blues/a little gold/yellow. Something that goes with our logo. We want our logo incorporated. Here is all the info you need:
Business name: RV Bone & Vitality Center
Location: 38517 North Willowmere Ave
Maple Ridge, FL 33990
Phone: 954-218-4063
Fax: 954-582-7341
Email: info@myrvbonecare.example

Names: Lydia Vance, M.D.
Fellowship Trained Hand and Arm Orthopaedic Surgeon

Ebo Dansu, M.D.
Board Certified Hip & Knee Replacement/General Orthopaedic Surgeon

Can decide what you want to put on the back. Maybe a slogan:
Grounded in Care. Centered on You

I am just going to upload our logo. The only thing is if we select you as the winning design, the location, and phone numbers may change. We will need your help to update that once fully solidified.

Industry/Entity Type

Medical

Contact Information for Business Card

Colors
0054AA
0677BA
7BADD7
CADEEF
E8F1F8
0094D4
00A9DD
6FCCEA
C7EBF8
E9F6FB

Requirements
Must have
• class, appeal,
Should not have
• We want to air on the side of masculine if we are looking at masculine vs. feminine feel. But we still want it classy, sophisticated, and something we will love

```html
<!DOCTYPE html>
<html lang="en">
<head>
<meta charset="utf-8">
<title>RV Bone &amp; Vitality Center – Business Card</title>
<link rel="stylesheet" href="https://fonts.googleapis.com/css2?family=Montserrat:wght@400;500;600;700&display=swap">
<style>
  :root {
    --navy: #253c7c;
    --cyan: #17b8de;
    --white: #ffffff;
    --shadow: rgba(40, 120, 110, 0.35);
  }
  * { margin: 0; padding: 0; box-sizing: border-box; }
  html, body { width: 894px; height: 1200px; overflow: hidden; background: var(--white); }
  body { position: relative; font-family: "Montserrat", sans-serif; }

  .card { position: absolute; left: 0; width: 894px; overflow: hidden; }
  .card svg.card-bg { position: absolute; inset: 0; }

  /* Front */
  .card-front { top: 0; height: 565px; }
  .front-shadow {
    position: absolute; left: 10px; top: 560px; width: 220px; height: 18px;
    background: var(--shadow); filter: blur(8px); border-radius: 50%;
  }
  .brand-front {
    position: absolute; left: 62px; top: 160px;
    display: flex; align-items: center; gap: 16px;
  }
  .brand-dot { width: 44px; height: 44px; border-radius: 50%; background: var(--navy); flex: none; }
  .brand-name {
    color: var(--navy); font-weight: 600; font-size: 24px; line-height: 1.15;
    letter-spacing: 0.5px; text-transform: uppercase;
  }
  .slogan {
    position: absolute; left: 464px; top: 234px;
    color: var(--cyan); font-weight: 700; font-size: 27px; line-height: 36px; letter-spacing: 0.6px;
  }
  .slogan span { display: block; }
  .slogan .indent { padding-left: 54px; }

  /* Back */
  .card-back { top: 630px; height: 570px; }
  .person { position: absolute; left: 87px; top: 98px; }
  .person-name {
    color: var(--cyan); font-weight: 700; font-size: 22px; letter-spacing: 0.6px;
    padding-bottom: 3px; border-bottom: 2px solid var(--cyan); display: inline-block; padding-right: 4px;
  }
  .person-title { color: var(--cyan); font-size: 13px; font-weight: 500; margin-top: 7px; letter-spacing: 0.1px; }

  .contacts { position: absolute; left: 85px; top: 180px; list-style: none; }
  .contacts li { display: flex; align-items: flex-start; gap: 10px; color: var(--cyan); font-size: 20px; font-weight: 500; line-height: 27px; margin-bottom: 24px; }
  .contacts li.address { margin-top: -4px; }
  .contacts svg { flex: none; width: 32px; height: 32px; margin-top: -2px; }
  .contacts li.address svg { margin-top: 12px; }

  .brand-back {
    position: absolute; left: 540px; top: 390px; width: 280px;
    display: flex; flex-direction: column; align-items: center; gap: 14px;
  }
  .brand-back .brand-name { text-align: center; font-size: 22px; }
</style>
</head>
<body>

<section class="card card-front">
  <svg class="card-bg" width="894" height="565" viewBox="0 0 894 565" aria-hidden="true">
    <rect width="894" height="565" fill="var(--cyan)"/>
    <path d="M100,0 H894 V502 H362 C330,502 312,480 312,450 C312,400 325,360 360,320 L100,320 Z" fill="var(--navy)"/>
    <path d="M0,0 H210 C330,0 410,80 406,200 C402,290 335,340 290,380 C230,440 205,500 200,565 H0 Z" fill="var(--white)"/>
  </svg>
  <div class="brand-front">
    <span class="brand-dot"></span>
    <span class="brand-name">RV Bone &amp;<br>Vitality<br>Center</span>
  </div>
  <p class="slogan"><span>“GROUNDED IN CARE.</span><span class="indent">CENTERED ON YOU”</span></p>
</section>
<div class="front-shadow"></div>

<section class="card card-back">
  <svg class="card-bg" width="894" height="570" viewBox="0 0 894 570" aria-hidden="true">
    <rect width="894" height="570" fill="var(--navy)"/>
    <path d="M285,570 C420,380 640,250 894,240 V570 Z" fill="var(--white)"/>
  </svg>

  <div class="person">
    <h1 class="person-name">LYDIA VANCE, M.D.</h1>
    <p class="person-title">Fellowship Trained Hand and Arm Orthopaedic Surgeon</p>
  </div>

  <ul class="contacts">
    <li>
      <svg viewBox="0 0 32 32" aria-label="Phone"><circle cx="16" cy="16" r="16" fill="var(--cyan)"/><path d="M11,8 l3,0 1.5,4 -2,1.5 c1,2.5 2.5,4 5,5 l1.5,-2 4,1.5 0,3 c0,1 -1,2 -2,2 C15,23 9,17 9,10 c0,-1 1,-2 2,-2z" fill="var(--navy)"/></svg>
      954-218-4063
    </li>
    <li>
      <svg viewBox="0 0 32 32" aria-label="Fax"><circle cx="16" cy="16" r="16" fill="var(--cyan)"/><rect x="11" y="8" width="10" height="5" fill="var(--navy)"/><rect x="8" y="13" width="16" height="8" rx="1.5" fill="var(--navy)"/><rect x="11" y="18" width="10" height="6" fill="var(--navy)" stroke="var(--cyan)" stroke-width="1"/></svg>
      954-582-7341
    </li>
    <li>
      <svg viewBox="0 0 32 32" aria-label="Email"><circle cx="16" cy="16" r="16" fill="var(--cyan)"/><rect x="8" y="10" width="16" height="12" rx="1" fill="var(--navy)"/><path d="M8,10 L16,17 L24,10 M8,22 L14,16 M24,22 L18,16" stroke="var(--cyan)" stroke-width="1.3" fill="none"/></svg>
      info@myrvbonecare.example
    </li>
    <li class="address">
      <svg viewBox="0 0 32 32" aria-label="Address"><circle cx="16" cy="16" r="16" fill="var(--cyan)"/><path d="M16,7 c-4,0 -6.5,3 -6.5,6.5 C9.5,18 16,25 16,25 s6.5,-7 6.5,-11.5 C22.5,10 20,7 16,7z" fill="var(--navy)"/><circle cx="16" cy="13.5" r="2.5" fill="var(--cyan)"/></svg>
      <span>38517 North Willowmere Ave<br>Maple Ridge, FL 33990</span>
    </li>
  </ul>

  <div class="brand-back">
    <span class="brand-dot"></span>
    <span class="brand-name">RV Bone &amp; Vitality Center</span>
  </div>
</section>

</body>
</html>
```